Video Editing Website - Wordpress Design Project

Hi There
I am setting up a Tribute Funeral Video and Home Video Editing Website for my Company. "Reel Harbor". This is to assist people with putting together their Videos and Photos with music to show at a Funeral or for Family Memories. I already have a domain www.reelharbor.com.au, but I have no host yet.

Some websites that already do this are http://www.quietlantern.com.au/tributes, http://www.cobaltframeworks.com.au/services/funeral-tribute-videos.html, and http://www.sundialkeepsakes.com.au/
These are examples not to cpy, but to get an idea of what I am offering so you can design accordingly.

I have a logo which is attached. You will see that the logo is mainly blue, so I would appreciate a website with that colour on the pages, but not ALL over the page.

I would like to upload videos occasionally from clipnest.com so I would appreciate that option incorporated.

Thank you lots.
Gareth

Target Market(s)

Families predominately in the 25-60 age range

Industry/Entity Type

It Company

Requirements
Must have
• *Ability to upload Videos from clipnest.com
*Ability for me to edit the content whenever I need to
*A contact page to send email messages to me

```html
<!DOCTYPE html>
<html lang="en">
<head>
<meta charset="utf-8">
<title>Reel Harbor – Tribute &amp; Home Video Editing</title>
<link href="https://fonts.googleapis.com/css2?family=PT+Sans:ital,wght@0,400;0,700;1,400&family=Roboto+Condensed:wght@400&display=swap" rel="stylesheet">
<style>
:root{
  --blue:#1f6fa8;
  --band:#21789f;
  --nav:#2b2b2b;
  --btn-light:#5ec4ee;
  --btn-dark:#2176b3;
  --text:#444;
  --muted:#777;
  --rule:#d6d6d6;
  --foot:#efefef;
}
*{box-sizing:border-box;margin:0;padding:0}
html,body{width:1199px;height:1200px;overflow:hidden;background:#fff}
body{font-family:"PT Sans",sans-serif;color:var(--text);position:relative}
.abs{position:absolute}
.brand{left:180px;top:58px;font-size:30px;color:var(--blue);font-weight:400;display:flex;align-items:center;gap:10px}
.brand-dot{width:22px;height:22px;border-radius:50%;background:var(--blue)}
.search{left:830px;top:77px;width:190px;height:21px;border:1px solid #ccc;background:#f6f6f6;font-size:8px;color:#777;padding:5px 9px;border-radius:2px}
.search svg{position:absolute;right:7px;top:4px}
.nav{left:180px;top:127px;width:840px;height:41px;background:var(--nav);border-radius:4px 4px 0 0;display:flex;justify-content:space-between;align-items:center;padding:0 24px;list-style:none}
.nav li{color:#fff;font-size:10px;text-transform:uppercase;letter-spacing:-.2px}
.hero{left:180px;top:168px;width:840px;height:363px;background:radial-gradient(ellipse at 62% 30%,#fff2c0 0%,#f6b24a 22%,#d8702a 50%,#9a3e12 80%,#6b2a0c 100%)}
.hero-figures{left:330px;top:4px;width:300px;height:359px;background:linear-gradient(180deg,#8c5a30,#4c2e18);border-radius:120px 120px 0 0;opacity:.75}
.hero-title{left:46px;top:128px;font-family:"Roboto Condensed",sans-serif;font-size:46px;color:#fff}
.hero-sub{left:48px;top:180px;font-family:"Roboto Condensed",sans-serif;font-size:28px;color:#1a1005;line-height:29px}
.pager{right:13px;bottom:12px;display:flex;gap:2px}
.pager i{width:10px;height:10px;background:#f3d8c5}
.pager i:first-child{background:#8a3a10}
.band{left:180px;top:531px;width:840px;height:102px;background:var(--band);color:#fff}
.band h1{position:absolute;left:25px;top:21px;font-size:21px;font-weight:400;text-transform:uppercase;letter-spacing:-.3px}
.band p{position:absolute;left:25px;top:55px;width:610px;font-size:8.5px;line-height:15px;text-transform:uppercase;font-weight:700;letter-spacing:-.2px}
.upload{position:absolute;left:670px;top:38px;width:149px;height:42px;background:linear-gradient(#7fd3f5,var(--btn-light));border:1px solid #a6e2f8;border-radius:3px;font-size:15px;text-transform:uppercase;text-align:center;line-height:40px}
h2.sec{position:absolute;font-size:18px;font-weight:400;color:var(--blue);text-transform:uppercase;letter-spacing:-.3px}
.video{left:180px;top:692px;width:316px;height:199px;background:linear-gradient(180deg,#10302e 0%,#3d4a2e 35%,#e4a420 55%,#1e3e3c 70%,#0b1f22 100%)}
.play{left:133px;top:65px;width:50px;height:48px;background:rgba(110,110,110,.7);border-radius:6px}
.play:after{content:"";position:absolute;left:17px;top:13px;border-left:18px solid #4fb6e6;border-top:11px solid transparent;border-bottom:11px solid transparent}
.controls{left:0;bottom:0;width:316px;height:22px;background:#1b1b1b;color:#ccc;font-size:7px;padding:6px 60px}
.progress{left:0;bottom:22px;width:316px;height:3px;background:#555}
.progress i{display:block;width:75px;height:3px;background:#c9211e}
.photo{background:linear-gradient(160deg,#b7c9a0,#6e7f58 55%,#4a3a34)}
.txt{position:absolute;font-size:9px;line-height:15.5px;color:var(--text)}
.more{position:absolute;width:85px;height:24px;background:linear-gradient(#4a9bd3,var(--btn-dark));border:1px solid #175b8e;border-radius:3px;color:#fff;font-size:10.5px;text-align:center;line-height:22px}
.arrow{position:absolute;width:15px;height:15px;border-radius:50%;background:#6b6b6b}
.arrow.light{width:20px;height:20px;background:#e2e2e2}
.arrow svg{position:absolute;left:0;top:0}
.t-head{left:902px;top:699px;font-size:10px;color:var(--blue);text-transform:uppercase}
.meta{position:absolute;font-size:8.5px;color:var(--blue);font-style:italic;line-height:15px}
.rule{left:180px;top:931px;width:840px;height:1px;background:var(--rule)}
.thumb{position:absolute;top:987px;width:156px;height:100px;background:#f2f2f2;box-shadow:0 8px 6px -6px rgba(0,0,0,.25);padding:7px}
.thumb div{width:100%;height:86px}
.footer{left:180px;top:1117px;width:840px;height:57px;background:linear-gradient(#e9e9e9,#fafafa)}
.footnav{position:absolute;left:24px;top:20px;display:flex;list-style:none;font-size:7.5px;text-transform:uppercase;color:#444}
.footnav li+li:before{content:"|";margin:0 12px}
.copy{position:absolute;left:24px;top:42px;font-size:7.5px;text-transform:uppercase;color:#444}
.follow{position:absolute;left:633px;top:35px;font-size:7.5px;text-transform:uppercase;color:#444}
.social{position:absolute;left:683px;top:25px;display:flex;gap:4px}
.social i{width:24px;height:24px;border-radius:50%}
</style>
</head>
<body>
<div class="abs brand"><span class="brand-dot"></span>Reel Harbor</div>
<div class="abs search">SEARCH :
  <svg width="12" height="12" viewBox="0 0 12 12"><circle cx="5" cy="5" r="3.6" fill="none" stroke="#bbb" stroke-width="1.4"/><line x1="7.6" y1="7.6" x2="11" y2="11" stroke="#bbb" stroke-width="1.6"/></svg>
</div>
<ul class="abs nav"><li>Home</li><li>About Us</li><li>Our Videos</li><li>Photo Gallery</li><li>Testimonials</li><li>Upload</li><li>Contact Us</li></ul>

<section class="abs hero" role="img" aria-label="Elderly couple embracing, seen from behind, in a golden wheat field at sunset">
  <div class="abs hero-figures"></div>
  <div class="abs hero-title">Reel Harbor</div>
  <div class="abs hero-sub">It was popularised in the<br>1960s with the release</div>
  <div class="abs pager"><i></i><i></i><i></i><i></i></div>
</section>

<section class="abs band">
  <h1>Welcome to Reel Harbor</h1>
  <p>It was popularised in the 1960s with the release of Lettrafold sheets containing lorem ipsum passages, and more recently with desktop publishing software like Norvel PageCraft including versions of lorem ipsum.</p>
  <div class="upload">Uplaod Videos</div>
</section>

<h2 class="sec" style="left:180px;top:656px">Tribute Funeral Video</h2>
<h2 class="sec" style="left:525px;top:656px">About Reel Harbor</h2>
<h2 class="sec" style="left:786px;top:656px">Testimonials</h2>
<div class="arrow" style="left:986px;top:661px"><svg width="15" height="15"><path d="M9 4 5.5 7.5 9 11" fill="none" stroke="#fff" stroke-width="1.5"/></svg></div>
<div class="arrow" style="left:1005px;top:661px"><svg width="15" height="15"><path d="M6 4 9.5 7.5 6 11" fill="none" stroke="#fff" stroke-width="1.5"/></svg></div>

<div class="abs video" role="img" aria-label="Video still of three crosses silhouetted against a stormy sunset over the sea">
  <div class="abs play"></div>
  <div class="abs progress"><i></i></div>
  <div class="abs controls">0:03 / 0:15</div>
</div>

<div class="abs photo" style="left:524px;top:693px;width:234px;height:97px;background:linear-gradient(180deg,#9fb88a 0%,#d99ab0 30%,#8a4e4a 60%,#5a6a3e 100%)" role="img" aria-label="Casket covered with pink and white flowers in a cemetery"></div>
<p class="txt" style="left:526px;top:802px;width:235px">It was popularised in the 1960s with the release of Lettrafold sheets containing Lorem Ipsum passages, and more recently with desktop publishing software like Norvel PageCraft including versions of Lorem Ipsum.</p>
<div class="more" style="left:527px;top:874px">Read More</div>

<div class="abs" style="left:786px;top:693px;width:97px;height:97px;background:linear-gradient(135deg,#e8e2dc,#8a6e5c 55%,#3a2a22)" role="img" aria-label="Hands clasped in prayer"></div>
<div class="abs t-head">It was popularised</div>
<p class="txt" style="left:901px;top:716px;width:120px">It was popularised in the 1960s with the release of Lettrafold sheets containing Lorem Ipsum passages, and more recently with desktop</p>
<p class="txt" style="left:788px;top:802px;width:235px">It was popularised in the 1960s with the release of Lettrafold sheets containing Lorem Ipsum passages...</p>
<p class="meta" style="left:787px;top:836px">Marlon Keats<br>Posted om 27 jun 2013</p>
<div class="more" style="left:788px;top:874px">Read More</div>

<div class="abs rule"></div>
<h2 class="sec" style="left:0;width:1199px;text-align:center;top:947px">Photo Gallery</h2>
<div class="arrow light" style="left:971px;top:948px"><svg width="20" height="20"><path d="M11.5 6 7.5 10 11.5 14" fill="none" stroke="#fff" stroke-width="1.5"/></svg></div>
<div class="arrow light" style="left:996px;top:948px"><svg width="20" height="20"><path d="M8.5 6 12.5 10 8.5 14" fill="none" stroke="#fff" stroke-width="1.5"/></svg></div>

<div class="thumb" style="left:180px"><div role="img" aria-label="White flower cross lying on grass" style="background:linear-gradient(150deg,#4e7a2e,#eef0e8 50%,#5c8a34)"></div></div>
<div class="thumb" style="left:351px"><div role="img" aria-label="Child in a dark coat beside white flowers at a graveside" style="background:linear-gradient(90deg,#2a2a2a 0%,#6a6a5a 40%,#e8ece0 75%,#7a8a6a)"></div></div>
<div class="thumb" style="left:523px"><div role="img" aria-label="Hands resting on fresh grass" style="background:linear-gradient(160deg,#3e6a22,#7ca040 50%,#d9b8a0 70%,#4a7026)"></div></div>
<div class="thumb" style="left:694px"><div role="img" aria-label="White floral wreath arch with pink roses on a grave" style="background:linear-gradient(180deg,#7a4a3e,#e6e6e0 45%,#d9a0b6 75%,#3e4a3a)"></div></div>
<div class="thumb" style="left:864px"><div role="img" aria-label="White and yellow flower arrangement among headstones" style="background:linear-gradient(180deg,#4a4a3a,#6a7a4a 45%,#e8eed8 70%,#3a5a22)"></div></div>

<footer class="abs footer">
  <ul class="footnav"><li>Home</li><li>About Us</li><li>Our Videos</li><li>Photo Gallery</li><li>Testimonials</li><li>Upload</li><li>Contact Us</li></ul>
  <div class="copy">Copyright © 2013. Reel Harbor. All rights reserved</div>
  <div class="follow">Follow us :</div>
  <div class="social">
    <i style="background:#2f6fb8" aria-label="Social link"></i>
    <i style="background:#4aa6de" aria-label="Social link"></i>
    <i style="background:#1f7aa8" aria-label="Social link"></i>
    <i style="background:#3a3a3a" aria-label="Social link"></i>
    <i style="background:#d02a2a" aria-label="Social link"></i>
  </div>
</footer>
</body>
</html>
```